Carpet cleaning company focused on high quality needs business cards

We are a growing company that just merged with another company and need to design a new business card. We do both residential as well as commercial cleaning. We do carpet, tile & grout, upholstery, hard floors, and stain & pet odor removal. We treat our customers like family and strive to achieve outstanding results with every job.

```html
<!DOCTYPE html>
<html lang="en">
<head>
<meta charset="utf-8">
<title>Brightwell Floorcare – Business Card</title>
<link href="https://fonts.googleapis.com/css2?family=Open+Sans:wght@400;600;700;800&display=swap" rel="stylesheet">
<style>
  :root {
    --stage: #222222;
    --paper: #ffffff;
    --ink: #1c1c1c;
    --ink-soft: #333333;
    --brand-red: #e8403a;
    --brand-red-deep: #d93630;
    --brand-red-light: #f06a62;
    --brand-red-pale: #f6b3ad;
    --faint: #f4f2f1;
  }
  * { box-sizing: border-box; margin: 0; padding: 0; }
  html, body {
    width: 1200px; height: 780px; overflow: hidden;
    background: var(--stage);
    font-family: "Open Sans", Arial, sans-serif;
  }
  .sheet {
    position: relative; width: 1200px; height: 780px;
    display: flex; align-items: center; justify-content: center; gap: 50px;
  }
  .card {
    position: relative; width: 540px; height: 310px;
    overflow: hidden; box-shadow: 0 12px 30px rgba(0,0,0,.45);
  }

  /* Front */
  .card--front { background: var(--paper); color: var(--ink); }
  .front__artwork {
    position: absolute; left: 28px; top: 24px; width: 104px; height: 92px;
    background: linear-gradient(135deg, var(--brand-red) 0%, var(--brand-red-light) 100%);
    border-radius: 2px;
  }
  .front__brand {
    position: absolute; left: 146px; top: 48px; width: 170px;
    font-weight: 800; font-size: 21px; line-height: 1.1; color: var(--ink);
  }
  .front__address {
    position: absolute; left: 28px; top: 132px;
    font-size: 13px; line-height: 1.45; color: var(--ink-soft);
  }
  .contact-list {
    position: absolute; left: 28px; top: 186px; list-style: none;
    font-size: 12.5px; line-height: 1.6; color: var(--ink-soft);
  }
  .contact-list li { display: flex; align-items: center; gap: 8px; }
  .contact-list svg { width: 11px; height: 11px; fill: var(--brand-red); flex: none; }
  .front__watermark {
    position: absolute; right: 40px; top: 60px; width: 230px; height: 250px;
    background: radial-gradient(ellipse at 50% 55%, var(--faint), rgba(244,242,241,0) 70%);
  }
  .front__person {
    position: absolute; right: 42px; top: 200px; text-align: right;
  }
  .person__name { font-size: 28px; font-weight: 700; line-height: 1.1; }
  .person__first { color: var(--brand-red); }
  .person__last { color: var(--ink); }
  .person__role { font-size: 15px; font-weight: 400; color: var(--ink-soft); margin-top: 2px; }
  .front__tab {
    position: absolute; right: 0; top: 196px; width: 16px; height: 70px;
    background: var(--brand-red);
  }

  /* Back */
  .card--back { background: var(--brand-red); }
  .back__pattern {
    position: absolute; inset: 0;
    background: linear-gradient(120deg, var(--brand-red-light) 0%, var(--brand-red) 45%, var(--brand-red-deep) 70%, var(--brand-red-pale) 100%);
  }
  .back__brand {
    position: absolute; left: 300px; top: 196px;
    display: flex; align-items: center; gap: 8px;
  }
  .back__mark { width: 22px; height: 22px; background: var(--paper); flex: none; }
  .back__name { font-size: 13px; font-weight: 800; color: var(--ink); line-height: 1.1; white-space: nowrap; }
</style>
</head>
<body>
  <main class="sheet">
    <section class="card card--front" aria-label="Business card front">
      <div class="front__artwork" role="img" aria-label="Company mascot illustration on a red square"></div>
      <div class="front__brand">Brightwell Floorcare</div>
      <p class="front__address">418 Linden Row, Suite 120<br>Arden, TX 75590</p>
      <ul class="contact-list">
        <li><svg viewBox="0 0 24 24" aria-hidden="true"><path d="M6.6 10.8a15 15 0 0 0 6.6 6.6l2.2-2.2a1 1 0 0 1 1-.25 11.4 11.4 0 0 0 3.6.57 1 1 0 0 1 1 1V20a1 1 0 0 1-1 1A17 17 0 0 1 3 4a1 1 0 0 1 1-1h3.5a1 1 0 0 1 1 1c0 1.25.2 2.45.57 3.57a1 1 0 0 1-.25 1z"/></svg>(555) 214-6830</li>
        <li><svg viewBox="0 0 24 24" aria-hidden="true"><path d="M2 5h20v14H2zm2 2v.5l8 5 8-5V7l-8 5z"/></svg>info@brightwellfloorcare.com</li>
        <li><svg viewBox="0 0 24 24" aria-hidden="true"><circle cx="12" cy="12" r="10"/></svg>www.brightwellfloorcare.com</li>
      </ul>
      <div class="front__watermark" role="img" aria-label="Faint large mascot illustration in the background"></div>
      <div class="front__person">
        <div class="person__name"><span class="person__first">Mirela</span> <span class="person__last">Dovhan</span></div>
        <div class="person__role">Managing Director</div>
      </div>
      <div class="front__tab"></div>
    </section>

    <section class="card card--back" aria-label="Business card back">
      <div class="back__pattern" role="img" aria-label="Repeating pattern of mascot silhouettes in shades of red"></div>
      <div class="back__brand">
        <span class="back__mark"></span>
        <span class="back__name">Brightwell Floorcare</span>
      </div>
    </section>
  </main>
</body>
</html>
```